Business card design for holistic health care clinic

We need a double-sided business card design for our holistic health care clinic that integrates our logo design and also its color scheme. My business is called Valmira. It is an integrative medicine clinic. You have already done the logo for me. Please ensure an elegant and upscale design that is not cluttered, but still has all the necessary information (please see below for details).

Target Market(s)

Wellness, fitness, rehabilitation for educated, well-traveled open-minded clients who are focused on natural, organic, balanced and preventive healthcare and lifestyle.

Industry/Entity Type

Medical

Contact Information for Business Card

Modern, clean.

Number of Pages Required

1 page

Font styles to use
Serif
Sans Serif

Colors

Designer to choose colors to be used in the design.

Requirements
Must have
• Logo on one side, all other information on the other side.
• Other information should include:
• Tobias Wrenfeld - DOE, CPT, LMT
• 4100 East Marrow Drive
• Austin, TX 78119
• 512 555 0148
• 818 555 0192
• info@ValmiraHealth.example
• t.wrenfeld@ValmiraHealth.example
Nice to have
• Darker background on front - but not totally black - shaded/dark gray.

```html
<!DOCTYPE html>
<html lang="en">
<head>
<meta charset="utf-8">
<title>Valmira – Business Card</title>
<link rel="stylesheet" href="https://fonts.googleapis.com/css2?family=Nunito:wght@700;800&family=Open+Sans:wght@400;600&display=swap">
<style>
  :root {
    --stage: #4a4a4a;
    --stage-top: #404040;
    --card-white: #ffffff;
    --brand-blue: #0b8fcf;
    --brand-blue-light: #1ba0dc;
    --ink: #1e1e1e;
    --on-blue: #ffffff;
  }
  * { margin: 0; padding: 0; box-sizing: border-box; }
  html, body {
    width: 1200px; height: 900px; overflow: hidden;
  }
  body {
    background: linear-gradient(180deg, var(--stage-top) 0%, var(--stage) 60%, #505050 100%);
    position: relative;
    font-family: "Open Sans", Arial, sans-serif;
  }
  .card {
    position: absolute;
    top: 306px;
    width: 440px;
    height: 271px;
    border-radius: 11px;
    overflow: hidden;
    box-shadow: 0 1px 3px rgba(0,0,0,0.35);
  }
  .card--info { left: 149px; background: var(--card-white); }
  .card--brand {
    left: 608px;
    background: var(--brand-blue);
  }
  .brand-glow {
    position: absolute; inset: 0;
    background: radial-gradient(ellipse at 50% 45%, var(--brand-blue-light) 0%, var(--brand-blue) 70%);
  }

  .wordmark {
    font-family: "Nunito", Arial, sans-serif;
    font-weight: 800;
    letter-spacing: 0.5px;
    line-height: 1;
  }
  .tagline {
    font-family: "Nunito", Arial, sans-serif;
    font-weight: 700;
    line-height: 1;
  }

  /* info side */
  .card--info .logo-block {
    position: absolute; right: 23px; top: 58px;
    text-align: right; color: var(--brand-blue);
  }
  .card--info .wordmark { font-size: 45px; }
  .card--info .tagline { font-size: 13.5px; margin-top: 6px; }

  .holder {
    position: absolute; left: 23px; right: 23px; top: 145px;
    display: flex; align-items: center; gap: 8px;
  }
  .holder__name {
    font-family: "Nunito", Arial, sans-serif;
    font-weight: 800; font-size: 15.5px;
    color: var(--brand-blue); letter-spacing: 0.3px;
    text-transform: uppercase; white-space: nowrap;
  }
  .holder__creds { font-size: 11.5px; color: var(--ink); white-space: nowrap; }
  .holder__rule { flex: 1; height: 1px; background: var(--brand-blue); }

  .contacts {
    position: absolute; left: 23px; top: 182px;
    list-style: none; font-size: 12px; color: var(--ink);
  }
  .contacts li { display: flex; align-items: center; gap: 6px; height: 16px; }
  .contacts svg { width: 10px; height: 10px; fill: var(--brand-blue); flex: none; }

  .address {
    position: absolute; right: 23px; top: 217px;
    text-align: right; font-size: 11.5px; line-height: 16px; color: var(--ink);
    font-style: normal;
  }

  /* brand side */
  .card--brand .logo-block {
    position: absolute; left: 0; right: 0; top: 120px;
    text-align: center; color: var(--on-blue);
  }
  .card--brand .wordmark { font-size: 48px; }
  .card--brand .tagline { font-size: 14.5px; margin-top: 6px; }
</style>
</head>
<body>

  <section class="card card--info" aria-label="Business card, contact side">
    <div class="logo-block">
      <div class="wordmark">VALMIRA</div>
      <div class="tagline">Integrative Holistic Medicine</div>
    </div>

    <div class="holder">
      <span class="holder__name">Tobias Wrenfeld</span>
      <span class="holder__creds">DOE, CPT, LMT</span>
      <span class="holder__rule"></span>
    </div>

    <ul class="contacts">
      <li>
        <svg viewBox="0 0 10 10" aria-hidden="true"><path d="M1 3.5C1 2 2.5 1.2 5 1.2S9 2 9 3.5L7.3 4 6.8 3H3.2L2.7 4ZM2.5 5h5l1 3.8H1.5Z"/></svg>
        512 555 0148
      </li>
      <li>
        <svg viewBox="0 0 10 10" aria-hidden="true"><path d="M3 0.5h4a.8.8 0 0 1 .8.8v7.4a.8.8 0 0 1-.8.8H3a.8.8 0 0 1-.8-.8V1.3A.8.8 0 0 1 3 .5Zm.2 1v6.2h3.6V1.5Z"/></svg>
        818 555 0192
      </li>
      <li>
        <svg viewBox="0 0 10 10" aria-hidden="true"><path d="M.5 2h9v6h-9Zm.8.6L5 5.4l3.7-2.8Z"/></svg>
        info@ValmiraHealth.example
      </li>
      <li>
        <svg viewBox="0 0 10 10" aria-hidden="true"><path d="M.5 2h9v6h-9Zm.8.6L5 5.4l3.7-2.8Z"/></svg>
        t.wrenfeld@ValmiraHealth.example
      </li>
    </ul>

    <address class="address">
      4100 East Marrow Drive<br>
      Austin, TX 78119
    </address>
  </section>

  <section class="card card--brand" aria-label="Business card, logo side">
    <div class="brand-glow" role="img" aria-label="Soft blue background where a faint enlarged brand emblem belongs"></div>
    <div class="logo-block">
      <div class="wordmark">VALMIRA</div>
      <div class="tagline">Integrative Holistic Medicine</div>
    </div>
  </section>

</body>
</html>
```